Halvorn Current Electric van design

Looking to design a wrap for a 2021 veltrana roamhaul high roof using orange black and dark grey colors like in the logo

```html
<!DOCTYPE html>
<html lang="en">
<head>
<meta charset="utf-8">
<title>Halvorn Current Electric – Van Wrap Layout</title>
<link rel="stylesheet" href="https://fonts.googleapis.com/css2?family=Montserrat:wght@500&family=Open+Sans:wght@400;700&display=swap">
<style>
  :root {
    --wrap-orange: #e05f3e;
    --wrap-black: #050505;
    --wrap-white: #ffffff;
    --page-bg: #ffffff;
  }
  * { margin: 0; padding: 0; box-sizing: border-box; }
  html, body {
    width: 1200px;
    height: 1010px;
    overflow: hidden;
    background: var(--page-bg);
  }
  .wrap-layout {
    position: absolute;
    left: 40px;
    top: 316px;
    width: 1120px;
    height: 377px;
    overflow: hidden;
  }
  .wrap-panels {
    position: absolute;
    inset: 0;
    width: 100%;
    height: 100%;
  }
  .brand {
    position: absolute;
    left: 580px;
    top: 50px;
    display: flex;
    align-items: center;
    gap: 24px;
  }
  .brand-dot {
    width: 116px;
    height: 116px;
    border-radius: 50%;
    background: var(--wrap-orange);
    flex: none;
  }
  .brand-name {
    font-family: "Montserrat", sans-serif;
    font-weight: 500;
    color: var(--wrap-white);
    font-size: 44px;
    line-height: 1.05;
    letter-spacing: 0.5px;
  }
  .services {
    position: absolute;
    top: 196px;
    left: 672px;
    display: flex;
    gap: 44px;
    list-style: none;
  }
  .services ul { list-style: none; }
  .services li {
    font-family: "Open Sans", sans-serif;
    font-size: 13px;
    color: var(--wrap-white);
    line-height: 21px;
    display: flex;
    align-items: center;
    gap: 7px;
    white-space: nowrap;
  }
  .service-arrow { width: 16px; height: 10px; flex: none; }
  .contact {
    position: absolute;
    left: 206px;
    top: 245px;
    text-align: center;
    color: var(--wrap-white);
    font-family: "Open Sans", sans-serif;
  }
  .contact-phone {
    font-weight: 700;
    font-size: 24px;
    letter-spacing: 0.5px;
    line-height: 1.2;
  }
  .contact-web {
    font-size: 11px;
    line-height: 1.3;
  }
</style>
</head>
<body>
<main class="wrap-layout" aria-label="Halvorn Current Electric van wrap, side layout">
  <svg class="wrap-panels" viewBox="0 0 1120 377" aria-hidden="true">
    <rect class="panel-orange" x="0" y="0" width="1120" height="377" fill="var(--wrap-orange)"/>
    <polygon class="divider-stripe" points="392,0 426,0 604,377 570,377" fill="var(--wrap-white)"/>
    <polygon class="panel-black" points="426,0 1120,0 1120,377 604,377" fill="var(--wrap-black)"/>
    <polyline class="accent-line" points="448,0 566,186 1120,186" fill="none" stroke="var(--wrap-white)" stroke-width="3"/>
  </svg>

  <div class="brand">
    <span class="brand-dot" aria-hidden="true"></span>
    <p class="brand-name">Halvorn<br>Current Electric</p>
  </div>

  <div class="services">
    <ul class="service-column">
      <li><svg class="service-arrow" viewBox="0 0 16 10" aria-hidden="true"><path d="M0 3h9V0l7 5-7 5V7H0z" fill="var(--wrap-orange)"/></svg>Generator Installation</li>
      <li><svg class="service-arrow" viewBox="0 0 16 10" aria-hidden="true"><path d="M0 3h9V0l7 5-7 5V7H0z" fill="var(--wrap-orange)"/></svg>Service Upgrades</li>
      <li><svg class="service-arrow" viewBox="0 0 16 10" aria-hidden="true"><path d="M0 3h9V0l7 5-7 5V7H0z" fill="var(--wrap-orange)"/></svg>Low Voltage Wiring</li>
      <li><svg class="service-arrow" viewBox="0 0 16 10" aria-hidden="true"><path d="M0 3h9V0l7 5-7 5V7H0z" fill="var(--wrap-orange)"/></svg>3-Phase Service</li>
    </ul>
    <ul class="service-column">
      <li><svg class="service-arrow" viewBox="0 0 16 10" aria-hidden="true"><path d="M0 3h9V0l7 5-7 5V7H0z" fill="var(--wrap-orange)"/></svg>Equipment Connections</li>
      <li><svg class="service-arrow" viewBox="0 0 16 10" aria-hidden="true"><path d="M0 3h9V0l7 5-7 5V7H0z" fill="var(--wrap-orange)"/></svg>Emergency Lighting</li>
      <li><svg class="service-arrow" viewBox="0 0 16 10" aria-hidden="true"><path d="M0 3h9V0l7 5-7 5V7H0z" fill="var(--wrap-orange)"/></svg>Code Violations</li>
      <li><svg class="service-arrow" viewBox="0 0 16 10" aria-hidden="true"><path d="M0 3h9V0l7 5-7 5V7H0z" fill="var(--wrap-orange)"/></svg>Warehouse Lighting</li>
    </ul>
  </div>

  <div class="contact">
    <p class="contact-phone">555.014.2290</p>
    <p class="contact-web">www.halvorncurrentelectric.com</p>
  </div>
</main>
</body>
</html>
```